Coastline Premier Retreats Business Card Design

Design a business card for Coastline Premier Retreats. Look at the website for colors and reference. Card should have logo, name, title, office number, mobile number, email, URL and a tagline like, "Luxury Hotel & Resort Email Marketing" (This might change).

https://www.coastlinepremierretreats.example

The rest I will leave up to your imagination.

Contact Information for Business Card

Logo, name, title, office number, mobile number, email, URL and a tagline like, "Luxury Hotel & Resort Email Marketing" (This might change).

```html
<!DOCTYPE html>
<html lang="en">
<head>
<meta charset="utf-8">
<title>Coastline Premier Retreats – Business Card</title>
<link rel="stylesheet" href="https://fonts.googleapis.com/css2?family=Arimo:wght@400;700&family=Questrial&display=swap">
<style>
  :root {
    --backdrop: #1e1e1e;
    --card-front: #f4f4f4;
    --card-back: #161616;
    --accent: #e46c12;
    --ink: #2b2b2b;
    --mark: #4a4a4a;
  }
  * { margin: 0; padding: 0; box-sizing: border-box; }
  html, body { width: 1200px; height: 1059px; overflow: hidden; }
  body {
    background: var(--backdrop);
    position: relative;
    font-family: "Arimo", Arial, sans-serif;
    color: var(--ink);
  }
  .card { position: absolute; overflow: hidden; }
  .card-front { left: 256px; top: 89px; width: 688px; height: 391px; background: var(--card-front); }
  .card-back  { left: 253px; top: 546px; width: 695px; height: 395px; background: var(--card-back); }

  .frame { position: absolute; left: 0; top: 0; }

  .identity {
    position: absolute; right: 400px; top: 146px; text-align: right; white-space: nowrap;
  }
  .person-name { font-weight: 700; font-size: 29px; color: var(--accent); line-height: 32px; letter-spacing: 0.2px; }
  .person-title { font-family: "Questrial", sans-serif; font-size: 16px; line-height: 20px; margin-top: 1px; }
  .office-address { font-size: 16px; line-height: 21px; margin-top: 9px; }

  .divider { position: absolute; left: 310px; top: 151px; width: 1px; height: 88px; background: var(--accent); }

  .contact-list { position: absolute; left: 334px; top: 146px; list-style: none; }
  .contact-list li { display: flex; align-items: center; height: 25px; font-size: 16px; white-space: nowrap; }
  .contact-list svg { width: 12px; height: 12px; margin-right: 7px; fill: var(--accent); flex: none; }

  .tagline {
    position: absolute; left: 0; width: 100%; top: 347px; text-align: center; font-size: 17px; line-height: 20px;
  }

  .brand-name {
    position: absolute; left: 0; width: 100%; top: 178px; text-align: center;
    font-family: "Arimo", Arial, sans-serif; font-weight: 700; font-size: 30px; letter-spacing: 3px;
    color: var(--mark); text-transform: uppercase;
  }
</style>
</head>
<body>
  <section class="card card-front" aria-label="Business card front">
    <svg class="frame" width="688" height="391" viewBox="0 0 688 391" aria-hidden="true">
      <path d="M178 358 H23 V22 H665 V358 H512" fill="none" stroke="var(--accent)" stroke-width="2"/>
    </svg>

    <div class="identity">
      <h1 class="person-name">MARCUS HALE</h1>
      <p class="person-title">CEO/Founder</p>
      <p class="office-address">Po Box, 48 B Harbor Rd<br>North America, AB 10000</p>
    </div>

    <div class="divider"></div>

    <ul class="contact-list">
      <li><svg viewBox="0 0 12 12"><path d="M3 0h6a1 1 0 0 1 1 1v10a1 1 0 0 1-1 1H3a1 1 0 0 1-1-1V1a1 1 0 0 1 1-1zm0.5 1.5v7.5h5V1.5zM6 9.8a.7.7 0 1 0 0 1.4a.7.7 0 0 0 0-1.4z"/></svg>555.204.7300</li>
      <li><svg viewBox="0 0 12 12"><path d="M0 4c0-2 3-3 6-3s6 1 6 3v1H9V3.5H3V5H0zM3 5.5h6l2 5.5H1z"/></svg>+34 600 000 412</li>
      <li><svg viewBox="0 0 12 12"><path d="M0 5l6-4 6 4v7H0zm1.2 1v4.8l3.4-2.4zm9.6 0l-3.4 2.4 3.4 2.4zM2 11h8L6 8.2z"/></svg>info@coastlinepremierretreats.example</li>
      <li><svg viewBox="0 0 12 12"><path d="M6 0a6 6 0 1 0 0 12A6 6 0 0 0 6 0zm-1 2c1 1 0 2 1 3s2 0 2 2-2 3-2 4C3 10 2 8 2 6c0-2 2-4 3-4z"/></svg>www.coastlinepremierretreats.example</li>
    </ul>

    <p class="tagline">Luxury Hotel &amp; Resort Email Marketing</p>
  </section>

  <section class="card card-back" aria-label="Business card back">
    <p class="brand-name">Coastline Premier Retreats</p>
  </section>
</body>
</html>
```